RWT Fittings Ltd Business Cards

We need a business card with our business logo. We provide window and door installations on high-rises in west coast British Colombia, Canada.

I would like my business information and details on one side of the card, and the other side the company name with logo

Target Market(s)

General Contractors

Industry/Entity Type

Construction

Contact Information for Business Card

one side i want my company name and logo in the dark theme logo that i provided

Requirements
Must have
• Marco Peltieri, 16045518293, RWTFittings@mailbox-demo.com, 1407-5194 Linden Row Burnaby BC, V5H 2K9, Owner & Manager

```html
<!DOCTYPE html>
<html lang="en">
<head>
<meta charset="utf-8">
<title>RWT Fittings Ltd Business Cards</title>
<link href="https://fonts.googleapis.com/css2?family=Open+Sans:wght@400;600;700;800&display=swap" rel="stylesheet">
<style>
  :root {
    --stage: #252525;
    --card-dark: #1f2026;
    --photo-top: #4a4540;
    --photo-mid: #2e2c2a;
    --photo-low: #1c1b1a;
    --brand-blue: #2aa9e6;
    --name-grey: #a3a3a6;
    --text-white: #f4f4f4;
    --divider: #8a8a8e;
  }
  * { box-sizing: border-box; margin: 0; padding: 0; }
  html, body {
    width: 1200px; height: 780px; overflow: hidden;
    background: var(--stage);
    font-family: "Open Sans", Arial, sans-serif;
  }
  .stage { position: relative; width: 1200px; height: 780px; }
  .card {
    position: absolute;
    width: 540px; height: 310px;
    border-radius: 22px;
    overflow: hidden;
    border-left: 7px solid var(--brand-blue);
    box-shadow: 0 18px 36px rgba(0,0,0,.55);
  }
  .card-front { left: 60px; top: 70px; }
  .card-back { left: 600px; top: 400px; background: var(--card-dark); }

  .front-backdrop {
    position: absolute; inset: 0;
    background:
      radial-gradient(ellipse at 75% 20%, var(--photo-top) 0%, transparent 60%),
      linear-gradient(160deg, var(--photo-mid) 0%, var(--photo-low) 100%);
  }
  .wordmark {
    position: absolute;
    display: flex; align-items: center; gap: 12px;
    color: var(--brand-blue);
    font-weight: 700;
    white-space: nowrap;
  }
  .wordmark-square { background: var(--brand-blue); flex: none; }
  .card-front .wordmark {
    left: 50%; top: 50%; transform: translate(-50%, -50%);
    font-size: 38px;
  }
  .card-front .wordmark-square { width: 34px; height: 34px; }

  .card-back .wordmark {
    left: 34px; top: 128px; font-size: 25px; gap: 10px;
  }
  .card-back .wordmark-square { width: 22px; height: 22px; }

  .divider {
    position: absolute; left: 258px; top: 70px;
    width: 1px; height: 140px; background: var(--divider);
  }
  .contact { position: absolute; left: 286px; top: 62px; }
  .person-name { font-size: 27px; font-weight: 800; line-height: 1.1; }
  .person-first { color: var(--brand-blue); }
  .person-last { color: var(--name-grey); }
  .person-title {
    color: var(--text-white); font-size: 14px; font-weight: 600; margin-top: 2px;
  }
  .contact-list { list-style: none; margin-top: 16px; }
  .contact-list li {
    display: flex; align-items: center; gap: 9px;
    color: var(--text-white); font-size: 12.5px; line-height: 1.75;
  }
  .contact-list svg { width: 13px; height: 13px; flex: none; fill: var(--brand-blue); }
  .address {
    position: absolute; left: 0; right: 0; bottom: 30px;
    text-align: center; color: var(--text-white); font-size: 15px;
  }
</style>
</head>
<body>
<main class="stage">

  <section class="card card-front" aria-label="Card front">
    <div class="front-backdrop" role="img" aria-label="Softly blurred dark office interior photograph with a plant"></div>
    <div class="wordmark"><span class="wordmark-square"></span>RWT Fittings Ltd</div>
  </section>

  <section class="card card-back" aria-label="Card back">
    <div class="wordmark"><span class="wordmark-square"></span>RWT Fittings Ltd</div>
    <div class="divider"></div>
    <div class="contact">
      <p class="person-name"><span class="person-first">Marco</span> <span class="person-last">Peltieri</span></p>
      <p class="person-title">Owner &amp; Manager</p>
      <ul class="contact-list">
        <li>
          <svg viewBox="0 0 24 24" aria-hidden="true"><path d="M6.6 10.8a15.1 15.1 0 0 0 6.6 6.6l2.2-2.2c.3-.3.7-.4 1-.2 1.1.4 2.3.6 3.6.6.6 0 1 .4 1 1V20c0 .6-.4 1-1 1A17 17 0 0 1 3 4c0-.6.4-1 1-1h3.5c.6 0 1 .4 1 1 0 1.3.2 2.5.6 3.6.1.3 0 .7-.2 1z"/></svg>
          (604) 551-8293
        </li>
        <li>
          <svg viewBox="0 0 24 24" aria-hidden="true"><path d="M2 5h20v14H2zm2 2v.5l8 5 8-5V7l-8 5z"/></svg>
          RWTFittings@mailbox-demo.com
        </li>
        <li>
          <svg viewBox="0 0 24 24" aria-hidden="true"><path d="M12 2a10 10 0 1 0 0 20 10 10 0 0 0 0-20zm0 2c1 0 2.3 2 2.8 5H9.2C9.7 6 11 4 12 4zM4.3 11h4.6a18 18 0 0 0 0 2H4.3a8 8 0 0 1 0-2zm6.6 0h2.2a16 16 0 0 1 0 2h-2.2a16 16 0 0 1 0-2zm4.2 0h4.6a8 8 0 0 1 0 2h-4.6a18 18 0 0 0 0-2zM9.2 15h5.6c-.5 3-1.8 5-2.8 5s-2.3-2-2.8-5z"/></svg>
          www.rwtfittings-demo.com
        </li>
      </ul>
    </div>
    <p class="address">1407-5194 Linden Row Burnaby BC, V5H 2K9</p>
  </section>

</main>
</body>
</html>
```